VOMRA Pty Ltd Business Card

Looking for a simple yet eye-catching double-sided business card design using my company logo on one side and contact details on the other.

Target Market(s)

Government

Industry/Entity Type

Communication Systems Engineering

Contact Information for Business Card

VOMRA Pty Ltd

Requirements
Nice to have
• Would be great to have a QR code so details can be scanned into contacts

```html
<!DOCTYPE html>
<html lang="en">
<head>
<meta charset="utf-8">
<title>VOMRA Pty Ltd Business Card</title>
<link href="https://fonts.googleapis.com/css2?family=Montserrat:wght@400;500;700;800&display=swap" rel="stylesheet">
<style>
  :root {
    --page-bg: #ecebe8;
    --slate: #37434b;
    --slate-deep: #27323a;
    --ink: #2f3b43;
    --paper: #ffffff;
    --shadow: rgba(20, 28, 34, 0.22);
  }
  * { margin: 0; padding: 0; box-sizing: border-box; }
  html, body {
    width: 1200px;
    height: 960px;
    overflow: hidden;
    background: var(--page-bg);
    font-family: "Montserrat", sans-serif;
  }
  .sheet {
    width: 1200px;
    height: 960px;
    display: flex;
    flex-direction: column;
    align-items: center;
    justify-content: center;
    gap: 46px;
  }
  .card {
    position: relative;
    width: 740px;
    height: 423px;
    border-radius: 40px;
    box-shadow: 0 14px 30px var(--shadow);
    overflow: hidden;
  }
  /* Back side */
  .card--back {
    background: var(--slate);
    display: flex;
    align-items: center;
    justify-content: center;
    gap: 34px;
  }
  .card--back .brand-mark {
    width: 120px;
    height: 120px;
    border-radius: 50%;
    background: var(--slate-deep);
  }
  .card--back .brand-name {
    font-weight: 800;
    font-size: 92px;
    letter-spacing: 4px;
    color: var(--slate-deep);
  }
  /* Front side */
  .card--front {
    background: var(--paper);
    color: var(--ink);
  }
  .front-brand {
    position: absolute;
    left: 60px;
    top: 0;
    height: 100%;
    display: flex;
    align-items: center;
    gap: 20px;
  }
  .front-brand .brand-mark {
    width: 74px;
    height: 74px;
    border-radius: 50%;
    border: 3px solid var(--ink);
  }
  .front-brand .brand-name {
    font-weight: 800;
    font-size: 58px;
    letter-spacing: 2px;
    color: var(--ink);
  }
  .divider {
    position: absolute;
    left: 430px;
    top: 78px;
    width: 2px;
    height: 268px;
    background: var(--ink);
  }
  .details {
    position: absolute;
    left: 456px;
    top: 86px;
    width: 270px;
  }
  .person-name {
    font-weight: 800;
    font-size: 25px;
    letter-spacing: 0.5px;
    line-height: 1.1;
  }
  .person-role {
    font-weight: 400;
    font-size: 17px;
    margin-top: 4px;
  }
  .contact-list {
    list-style: none;
    margin-top: 26px;
  }
  .contact-list li {
    display: flex;
    align-items: center;
    gap: 9px;
    font-size: 15.5px;
    line-height: 1.65;
  }
  .contact-list svg {
    width: 14px;
    height: 14px;
    flex: none;
  }
  .address {
    margin-top: 22px;
    font-size: 15.5px;
    line-height: 1.4;
  }
</style>
</head>
<body>
  <main class="sheet">
    <section class="card card--back" aria-label="Card back">
      <span class="brand-mark"></span>
      <span class="brand-name">VOMRA</span>
    </section>

    <section class="card card--front" aria-label="Card front">
      <div class="front-brand">
        <span class="brand-mark"></span>
        <span class="brand-name">VOMRA</span>
      </div>

      <div class="divider"></div>

      <div class="details">
        <h1 class="person-name">DANIEL HARPER</h1>
        <p class="person-role">Managing Director</p>

        <ul class="contact-list">
          <li>
            <svg viewBox="0 0 24 24" aria-hidden="true"><path fill="#2f3b43" d="M6.6 10.8a15.1 15.1 0 0 0 6.6 6.6l2.2-2.2c.3-.3.7-.4 1-.2 1.1.4 2.3.6 3.6.6.6 0 1 .4 1 1V20c0 .6-.4 1-1 1A17 17 0 0 1 3 4c0-.6.4-1 1-1h3.5c.6 0 1 .4 1 1 0 1.3.2 2.5.6 3.6.1.3 0 .7-.2 1z"/></svg>
            123 987 654
          </li>
          <li>
            <svg viewBox="0 0 24 24" aria-hidden="true"><path fill="#2f3b43" d="M2 5h20v14H2z"/><path fill="none" stroke="#fff" stroke-width="2" d="M2 6l10 7 10-7"/></svg>
            admin@vomra.com.au
          </li>
          <li>
            <svg viewBox="0 0 24 24" aria-hidden="true"><circle cx="12" cy="12" r="10" fill="#2f3b43"/><path fill="none" stroke="#fff" stroke-width="1.5" d="M2 12h20M12 2c3 3 3 17 0 20M12 2c-3 3-3 17 0 20"/></svg>
            www.vomra.com.au
          </li>
        </ul>

        <p class="address">45-47 Harbour Lane Redfern<br>NSW 2016 Australia</p>
      </div>
    </section>
  </main>
</body>
</html>
```